Orvane Mechanical - Letterhead

We are a plumbing and hvac company based in Calgary. This letterhead will be on our quotes, invoices, preventative maintenance proposals etc.

```html
<!DOCTYPE html>
<html lang="en">
<head>
<meta charset="utf-8">
<title>Orvane Mechanical – Letterhead</title>
<link rel="stylesheet" href="https://fonts.googleapis.com/css2?family=Open+Sans:wght@400;600;800&display=swap">
<style>
  :root{
    --bg:#e4e4e4;
    --paper:#ffffff;
    --brand-blue:#2f6db8;
    --brand-orange:#e8582a;
    --ink:#1e1e1e;
    --ink-soft:#333333;
    --rule:#d6dde8;
    --sign-tone:#d9d9d9;
  }
  *{box-sizing:border-box;margin:0;padding:0}
  html,body{width:1200px;height:945px;overflow:hidden;background:var(--bg)}
  body{font-family:"Open Sans",Arial,sans-serif;color:var(--ink)}
  .letterhead{
    position:absolute;left:265px;top:18px;width:670px;height:909px;
    background:var(--paper);box-shadow:0 2px 10px rgba(0,0,0,.12);overflow:hidden;
  }
  .top-band{position:absolute;left:0;top:0;width:100%;height:16px;background:var(--brand-blue)}
  .top-accent{position:absolute;left:0;top:16px;width:100%;height:5px;background:var(--brand-orange)}
  .header{
    position:absolute;left:46px;right:46px;top:70px;height:90px;
    display:flex;align-items:center;justify-content:space-between;
    border-bottom:1px solid var(--rule);padding-bottom:22px;
  }
  .brand{display:flex;align-items:center;gap:10px}
  .brand-dot{width:26px;height:26px;border-radius:50%;background:var(--brand-orange)}
  .brand-name{font-weight:800;font-size:25px;color:var(--brand-blue);letter-spacing:.5px;text-transform:uppercase;line-height:1}
  .contact{font-size:9px;line-height:13px;color:var(--ink-soft);list-style:none}
  .contact li{display:flex;align-items:center;gap:5px}
  .contact svg{width:8px;height:8px;flex:none}
  .contact .address{margin-top:5px;padding-left:13px;display:block}
  .letter-body{position:absolute;left:62px;top:270px;width:560px}
  .salutation{font-weight:600;font-size:14px;margin-bottom:14px}
  .letter-body p{font-size:12.5px;line-height:16.5px;color:var(--ink-soft);margin-bottom:17px;padding-left:14px}
  .signature{position:absolute;left:76px;top:745px;width:150px;height:52px;background:var(--sign-tone);border-radius:3px}
</style>
</head>
<body>
  <main class="letterhead">
    <div class="top-band"></div>
    <div class="top-accent"></div>

    <header class="header">
      <div class="brand">
        <span class="brand-dot"></span>
        <span class="brand-name">Orvane Mechanical</span>
      </div>
      <ul class="contact">
        <li><svg viewBox="0 0 10 10"><path fill="var(--brand-orange)" d="M2 0h2l1 3-1.5 1a6 6 0 0 0 2.5 2.5L7 5l3 1v2a2 2 0 0 1-2 2C4 10 0 6 0 2a2 2 0 0 1 2-2z"/></svg>855-210-7788</li>
        <li><svg viewBox="0 0 10 10"><rect x="0" y="2" width="10" height="7" fill="var(--brand-orange)"/><path d="M0 2l5 4 5-4" stroke="#fff" fill="none"/></svg>info@orvanemechanical.com</li>
        <li><svg viewBox="0 0 10 10"><circle cx="5" cy="5" r="4.5" fill="var(--brand-orange)"/><circle cx="5" cy="5" r="2" fill="#fff"/></svg>www.orvanemechanical.com</li>
        <li class="address">Po. Box 56, Street Name,<br>City Name, Zip Code - 00000</li>
      </ul>
    </header>

    <section class="letter-body">
      <h1 class="salutation">Dear Mr. Hale,</h1>
      <p>Lorem Ipsum is simply dummy text of the printing and typesetting industry. Lorem Ipsum has been the industry's standard dummy text ever since the 1500s, when an unknown printer took a galley of type and scrambled it to make a type specimen book. It has survived not only five centuries, but also the leap into electronic typesetting, remaining essentially unchanged.</p>
      <p>The standard chunk of Lorem Ipsum used since the 1500s is reproduced below for those interested. Sections 1.10.32 and 1.10.33 from "de Finibus Bonorum et Malorum" by Cicero are also reproduced in their exact original form, accompanied by English versions from the 1914 translation by H. Rackham</p>
      <p>Lorem Ipsum is simply dummy text of the printing and typesetting industry. Lorem Ipsum has been the industry's standard dummy text ever since the 1500s, when an unknown printer took a galley of type and scrambled it to make a type specimen book. It has survived not only five centuries, but also the leap into electronic typesetting, remaining essentially unchanged. It was popularised in the</p>
      <p>The standard chunk of Lorem Ipsum used since the 1500s is reproduced below for those interested. Sections 1.10.32 and 1.10.33 from "de Finibus Bonorum et Malorum" by Cicero are also reproduced in their exact original form, accompanied by English versions from the 1914 translation by H. Rackham</p>
      <p>The standard chunk of Lorem Ipsum used since the 1500s is reproduced below for those interested. Sections 1.10.32 and 1.10.33 from "de Finibus Bonorum et Malorum" by Cicero are also reproduced in their exact original form.</p>
    </section>

    <div class="signature" role="img" aria-label="Handwritten signature of the sender"></div>
  </main>
</body>
</html>
```